Leadership training for women Business + Spirit

I need a flyer for a leadership training to hand out after I've been doing public speaking. I would also like to send it as a PDF. so maybe A4 is a good size. I will probably also need a brochure, with some more in depth information, but to start with I like to just give them something so they get inspired to contact me for more information. You can see more of my style on www.brightmeadow.se . Its a training that combines business with spirit, heart with intellect. We focus both on strict leadership skills such as Setting objectives aligned with strategy, assess performance and spiritual practices such as meditation, connecting with your unique essence. I like the deign to communicate business and professional together with warmth, life and joy. Colourful with style. Empowerment. The attached style guide does not have to be followed strictly but please use it in combination with my site www.brightmeadow.se I've the logo in many different sizes. I've added the smallest one below. Use any images that you think might fit, doesn't have to be from my website, it could be from your resources. I've added some other images here in the brief too, I have many more but can't attach all of it :-).
Target Market(s)
Women in leadership positions age 30 - 60
Industry/Entity Type
Leadership
Look and feel

```html
<!DOCTYPE html>
<html lang="sv">
<head>
<meta charset="utf-8">
<title>Bright Meadow Ledarskap – flyer</title>
<link href="https://fonts.googleapis.com/css2?family=Oswald:wght@500;600&family=Lato:wght@400;700&display=swap" rel="stylesheet">
<style>
  :root{
    --navy:#1c2f4b;
    --orange:#ee7d16;
    --ink:#1d1d1d;
    --white:#ffffff;
    --stage:#2f2c29;
    --sand:#9a8d80;
    --sea:#c9d3d8;
  }
  *{box-sizing:border-box;margin:0;padding:0}
  html,body{width:1200px;height:1200px;overflow:hidden;background:var(--stage)}
  .flyer{position:absolute;left:172px;top:0;width:856px;height:1200px;background:var(--white);overflow:hidden;font-family:'Lato',sans-serif;color:var(--ink)}
  .flyer > *{z-index:2}
  .header-bg{position:absolute;left:0;top:0;width:856px;height:425px;z-index:1}
  .headline{position:absolute;left:47px;top:30px;width:800px;font-family:'Oswald',sans-serif;font-weight:600;font-size:26px;line-height:31px;color:var(--white);text-transform:uppercase;letter-spacing:-.4px}
  .headline-rule{position:absolute;left:47px;top:99px;width:511px;height:4px;background:var(--orange)}
  .intro{position:absolute;left:50px;top:117px;width:780px;font-size:13px;line-height:16.8px;color:var(--white)}
  .focus-list{position:absolute;left:44px;top:259px;width:640px;list-style:none;color:var(--white);font-size:13px;line-height:17px}
  .focus-list li{position:relative;padding-left:17px;margin-bottom:16.5px}
  .focus-list li::before{content:"";position:absolute;left:2px;top:4px;width:6px;height:6px;border-top:2.5px solid var(--orange);border-right:2.5px solid var(--orange);transform:rotate(45deg)}
  .brand-mark{position:absolute;left:710px;top:282px;width:90px;text-align:center;color:var(--white);font-size:12px;font-weight:700}
  .brand-mark .dot{display:block;margin:0 auto 6px;width:56px;height:56px;border-radius:50%;border:1.5px solid #8fa3bd}
  .leader-title{position:absolute;left:36px;top:462px;font-family:'Oswald',sans-serif;font-weight:500;font-size:20px;color:var(--orange)}
  .leader-body{position:absolute;left:36px;top:510px;width:515px;display:flex;flex-direction:column;gap:17px}
  .leader-text{font-size:12.6px;line-height:16.9px;color:var(--ink)}
  .portrait{position:absolute;left:592px;top:437px;width:189px;height:284px;border:4px solid var(--navy);background:linear-gradient(160deg,#7a5a4c 0%,#5b4840 45%,#2a2c33 75%,#e8e4de 100%)}
  .guarantee{position:absolute;left:0;top:736px;width:856px;height:41px;background:var(--orange);color:var(--white);font-family:'Oswald',sans-serif;font-weight:600;font-size:18.5px;line-height:41px;text-align:center;letter-spacing:-.2px}
  .promise{position:absolute;left:43px;top:795px;font-weight:700;font-size:19px;color:var(--navy)}
  .promise-rule{position:absolute;left:43px;top:835px;width:597px;height:3px;background:var(--orange)}
  .extras-lead{position:absolute;left:48px;top:853px;font-size:14.5px}
  .extras{position:absolute;top:877px;list-style:none;font-size:14.5px;line-height:25px}
  .extras li::before{content:"•";margin:0 8px 0 1px}
  .extras.left{left:48px}
  .extras.right{left:378px}
  .flyer > .shore{position:absolute;left:0;top:910px;width:856px;height:255px;z-index:1;background:linear-gradient(to bottom,rgba(255,255,255,1) 0%,rgba(255,255,255,1) 10%,rgba(255,255,255,0) 38%),linear-gradient(100deg,var(--sand) 0%,#b2a597 45%,var(--sea) 62%,#e9eef0 80%,#a9b8c0 100%)}
  .footer{position:absolute;left:0;top:1163px;width:856px;height:37px;background:var(--navy);color:var(--white);font-size:17px;letter-spacing:.6px;display:flex;align-items:center;justify-content:center;gap:12px}
</style>
</head>
<body>
<div class="flyer">
  <svg class="header-bg" viewBox="0 0 856 425" aria-hidden="true">
    <path d="M0 0H856V372Q460 445 0 388Z" fill="var(--navy)"/>
  </svg>
  <h1 class="headline">Är du kvinna och vill du förbättra ditt ledarskap, öka dina resultat och bygga dig genuint starkare för var dag?</h1>
  <div class="headline-rule"></div>
  <p class="intro">Den här ledarskapsutbildningen är till för dig som är kvinna och ledare till yrket, gillar att leverera och nu vill hitta platsen där du utvecklas som själ likväl som chef.<br>Utbildningen varvar det personliga med det professionella så att du samtidigt som du ökar din arbetsprestation även fördjupar kontakten med ditt inre, får nya perspektiv, hanterar stressen konstruktivt och skapar ett liv med god balans - både på arbetet och livet som helhet.<br>Utbildningen består av 2 fristående moduler på 2 + 3 dagar + online uppföljning. Man kan alltså välja att göra 2 eller 5 dagar, alltefter behov. Modulerna är uppbyggda så att innehållet passar oavsett om du leder projekt, medarbetare eller större enheter:</p>
  <ul class="focus-list">
    <li>Vi arbetar med att effektivisera arbetstiden genom analys, prioriteringar, mål och time management.</li>
    <li>Vi arbetar med kommunikation genom coaching, feedback, svåra samtal och stakeholder management.</li>
    <li>Vi arbetar med stresshantering genom avslappning, mindfulness, mental träning och tankens kraft.</li>
    <li>Vi arbetar med inre kontakt och den feminina essensen genom meditationer, samtal och övningar för ökad medvetenhet och djupare förankring i själ och hjärta.</li>
  </ul>
  <div class="brand-mark"><span class="dot"></span>Bright Meadow</div>

  <h2 class="leader-title">Kursledaren Karin Lindvall Berg :</h2>
  <div class="leader-body">
    <p class="leader-text">Jag är en modern mystiker och ledarskapsutvecklare som de senaste 16 åren har tillhandahållit tusentals timmar med coaching, kurser och föreläsningar. Antingen har det varit ledarskapsutbildningar med fokus på prestation och leverans på t.ex. Solvik Bank, Mejerigården, Brygghuset Norr, Stegsko, Tryggvall, Vindkraft Nord, Livsbutiken m.fl. eller utbildningar med fokus på meditation och den feminina essensen. Nu är det dags att kombinera dessa områden!</p>
    <p class="leader-text">Med Bright Meadow Ledarskap vill jag ge ett rum till just kvinnor i ledande positioner att ta sig an det arbete och de enorma möjligheter som ligger framför oss om vi fokuserar på vårt ledarskap, omvandlar stressen till kraft, låter det djupa varandet guida oss och öppnar vårt sinne för den kreativitet och struktur som behövs för att möta morgondagens utmaningar.</p>
  </div>
  <div class="portrait" role="img" aria-label="Porträttfoto av kursledaren framför en tegelvägg"></div>

  <div class="guarantee">PENGAR-TILLBAKA-GARANTI: Om du under utbildning inte är nöjd så får du 100 % tillbaka.</div>

  <div class="shore" role="img" aria-label="Foto av en sandstrand med ord skrivna i sanden och vågor som sköljer in"></div>

  <p class="promise">Du kommer att lämna utbildningen påfylld, inspirerad och förberedd!</p>
  <div class="promise-rule"></div>
  <p class="extras-lead">Dessutom får du med dig :</p>
  <ul class="extras left">
    <li>Personlig handlings -och utvecklingsplan</li>
    <li>Konkreta verktyg för ditt välmående</li>
  </ul>
  <ul class="extras right">
    <li>Konkreta verktyg för ledarskapet</li>
    <li>Nätverk av likasinnade kvinnor</li>
  </ul>

  <div class="footer">
    <svg width="13" height="13" viewBox="0 0 14 14" aria-hidden="true"><g fill="none" stroke="var(--orange)" stroke-width="1.3"><circle cx="7" cy="7" r="6"/><ellipse cx="7" cy="7" rx="2.6" ry="6"/><path d="M1 7H13M2 4H12M2 10H12"/></g></svg>
    <span>www.brightmeadow.se</span>
  </div>
</div>
</body>
</html>
```